Modern Label for cleaning products for the brand Vorlix

We need a label design for our line of cleaning products. The label should feature our logo and an image to identify the product's intended use. I've added our logo and an image for use. This only concerns the design of the label on the front of the bottle.

Label dimensions:
Label 1 (500ml bottle with spray): width 58mm x height 115mm
Label 2: (1L bottle): width 73mm x height 140mm
The design must be consistent for both bottles which you find in the pictures.

The bottles to be labeled are white. See the attachment for a photo of the bottles.

The photo must also appear on the label to identify the product's intended use.

Product information:
Brand: Vorlix
Product: Sanitary Cleaner

This text must be placed on the label:
"Cleans, descales & freshens. followed with this text: "Ideal for quick and powerful cleaning. A ready-to-use product for everyday use."

- Mention the seperate USP's: Sanitary, Bathroom, Toilet, Wet areas

Appearance: This is a consumer product, but it must have a professional appearance. We would like to see a design that use the color blue from our logo.

Target Market(s)

Consumers who take care of their homes and want to maintain it the correct (professional) way

Font styles to use
Sans Serif

Colors
0054AA
0677BA
7BADD7
CADEEF
E8F1F8

Requirements
Must have
• USP's + use of image and logo + blend in 1 design
Nice to have
• Keep the color of the logo in the design
Should not have
• Comic sans

```html
<!DOCTYPE html>
<html lang="en">
<head>
<meta charset="utf-8">
<title>Vorlix Sanitary Cleaner – Front Labels</title>
<link rel="stylesheet" href="https://fonts.googleapis.com/css2?family=Oswald:wght@300;400;500;600&display=swap">
<style>
  :root {
    --canvas: #ffffff;
    --label-cream: #ebf1d4;
    --brand-blue: #0054aa;
    --blue-mid: #0677ba;
    --ink: #1f1f1f;
    --leaf: #3aa53a;
    --leaf-dark: #2f7f2f;
    --tile: #b9d98f;
    --photo-light: #d6f0a8;
    --photo-mid: #7ed36a;
    --photo-deep: #2fb24a;
  }
  * { box-sizing: border-box; margin: 0; padding: 0; }
  html, body {
    width: 1200px; height: 1200px; overflow: hidden;
    background: var(--canvas);
    font-family: "Oswald", "Arial Narrow", sans-serif;
  }
  .label-set {
    position: relative; width: 1200px; height: 1200px;
    display: flex; align-items: flex-end; justify-content: center;
    gap: 60px; padding-bottom: 320px;
  }
  .label {
    width: 26.1em;
    background: var(--label-cream);
    border-radius: 0.6em;
    overflow: hidden;
    display: flex; flex-direction: column; align-items: center;
    text-align: center;
    box-shadow: 0 0.3em 1.2em rgba(0,0,0,0.12);
  }
  .label--500ml { font-size: 10px; height: 51.7em; }
  .label--1l { font-size: 12.6px; height: 50em; }

  .label__photo {
    width: 100%; height: 48.6%; flex: none;
    background:
      radial-gradient(ellipse at 30% 55%, var(--photo-deep) 0%, rgba(47,178,74,0) 55%),
      radial-gradient(ellipse at 75% 20%, var(--photo-light) 0%, rgba(214,240,168,0) 60%),
      linear-gradient(135deg, var(--photo-mid), #a8e08a 60%, var(--photo-light));
  }
  .brand {
    margin-top: -2.3em;
    display: flex; flex-direction: column; align-items: center;
  }
  .brand__dot {
    width: 4.6em; height: 4.6em; border-radius: 50%;
    background: var(--brand-blue);
  }
  .brand__name {
    font-weight: 600; font-size: 2em; line-height: 1.1;
    color: var(--ink); letter-spacing: 0.02em; margin-top: 0.05em;
  }
  .product-title {
    font-weight: 600; font-size: 2.6em; line-height: 1;
    color: var(--brand-blue); margin-top: 0.45em; letter-spacing: 0.005em;
  }
  .product-claims {
    font-weight: 400; font-size: 1.45em; color: var(--ink);
    letter-spacing: 0.06em; margin-top: 0.1em;
  }
  .fragrance {
    display: flex; align-items: center; gap: 0.5em;
    font-size: 0.95em; font-weight: 400; color: var(--leaf);
    margin-top: 1.5em;
  }
  .fragrance__mark {
    width: 2em; height: 2em; border-radius: 50%; background: #8cc63f;
  }
  .description {
    font-weight: 300; font-size: 1.05em; line-height: 1.45;
    color: var(--ink); margin-top: 1.2em;
  }
  .use-areas {
    display: flex; gap: 0.75em; margin-top: 0.9em; list-style: none;
  }
  .use-area { display: flex; flex-direction: column; align-items: center; }
  .use-area__tile {
    width: 4.3em; height: 3.5em; border-radius: 0.5em;
    background: var(--tile); display: flex; align-items: center; justify-content: center;
  }
  .use-area__tile svg { width: 2.4em; height: 2.4em; }
  .use-area__name {
    font-size: 0.6em; font-weight: 400; color: var(--ink); margin-top: 0.5em;
  }
  .volume {
    margin-top: auto; margin-bottom: 1.2em;
    font-weight: 300; font-size: 1.35em; color: var(--ink);
  }
</style>
</head>
<body>
<main class="label-set">

  <section class="label label--500ml" aria-label="500 ml spray bottle front label">
    <div class="label__photo" role="img" aria-label="Soft-focus close-up of a green dandelion seed head"></div>
    <div class="brand">
      <span class="brand__dot"></span>
      <span class="brand__name">vorlix</span>
    </div>
    <h1 class="product-title">SANITARY CLEANER</h1>
    <p class="product-claims">CLEANS · DESCALES · FRESHENS</p>
    <p class="fragrance">POTPOURRI <span class="fragrance__mark"></span> FRAGRANCE</p>
    <p class="description">Ideal for quick and powerful cleaning.<br>A ready-to-use product for everyday use.</p>
    <ul class="use-areas">
      <li class="use-area"><span class="use-area__tile"><svg viewBox="0 0 24 24" fill="#2f7f2f"><rect x="2" y="12" width="13" height="5" rx="2"/><rect x="4" y="17" width="2" height="3"/><rect x="11" y="17" width="2" height="3"/><rect x="15" y="4" width="7" height="5" fill="none" stroke="#2f7f2f" stroke-width="1.5"/><rect x="17.5" y="10" width="2" height="10"/><rect x="15" y="11" width="7" height="2"/></svg></span><span class="use-area__name">BATHROOM</span></li>
      <li class="use-area"><span class="use-area__tile"><svg viewBox="0 0 24 24" fill="#2f7f2f"><path d="M5 22V8a5 5 0 0 1 10 0" fill="none" stroke="#2f7f2f" stroke-width="1.8"/><circle cx="15" cy="11" r="1"/><circle cx="18" cy="12" r="1"/><circle cx="14" cy="14" r="1"/><circle cx="17" cy="15" r="1"/><circle cx="20" cy="15" r="1"/><circle cx="16" cy="18" r="1"/><circle cx="19" cy="18" r="1"/></svg></span><span class="use-area__name">SHOWER</span></li>
      <li class="use-area"><span class="use-area__tile"><svg viewBox="0 0 24 24" fill="#2f7f2f"><rect x="14" y="3" width="6" height="9" rx="1"/><path d="M3 11h17c0 4-3 6-6 6l1 4H8l1-4c-3-1-6-3-6-6z"/></svg></span><span class="use-area__name">TOILET</span></li>
      <li class="use-area"><span class="use-area__tile"><svg viewBox="0 0 24 24" fill="#2f7f2f"><rect x="2" y="3" width="5" height="4"/><rect x="8" y="3" width="4" height="4"/><path d="M15 7l3-4 3 4z"/><rect x="2" y="10" width="9" height="4"/><rect x="2" y="16" width="9" height="5"/><rect x="13" y="10" width="9" height="11" fill="none" stroke="#2f7f2f" stroke-width="1.5"/><rect x="15" y="14" width="5" height="4"/></svg></span><span class="use-area__name">KITCHEN</span></li>
    </ul>
    <p class="volume">500Ml (17 Oz.)</p>
  </section>

  <section class="label label--1l" aria-label="1 litre bottle front label">
    <div class="label__photo" role="img" aria-label="Soft-focus close-up of a green dandelion seed head"></div>
    <div class="brand">
      <span class="brand__dot"></span>
      <span class="brand__name">vorlix</span>
    </div>
    <h2 class="product-title">SANITARY CLEANER</h2>
    <p class="product-claims">CLEANS · DESCALES · FRESHENS</p>
    <p class="fragrance">POTPOURRI <span class="fragrance__mark"></span> FRAGRANCE</p>
    <p class="description">Ideal for quick and powerful cleaning.<br>A ready-to-use product for everyday use.</p>
    <ul class="use-areas">
      <li class="use-area"><span class="use-area__tile"><svg viewBox="0 0 24 24" fill="#2f7f2f"><rect x="2" y="12" width="13" height="5" rx="2"/><rect x="4" y="17" width="2" height="3"/><rect x="11" y="17" width="2" height="3"/><rect x="15" y="4" width="7" height="5" fill="none" stroke="#2f7f2f" stroke-width="1.5"/><rect x="17.5" y="10" width="2" height="10"/><rect x="15" y="11" width="7" height="2"/></svg></span><span class="use-area__name">BATHROOM</span></li>
      <li class="use-area"><span class="use-area__tile"><svg viewBox="0 0 24 24" fill="#2f7f2f"><path d="M5 22V8a5 5 0 0 1 10 0" fill="none" stroke="#2f7f2f" stroke-width="1.8"/><circle cx="15" cy="11" r="1"/><circle cx="18" cy="12" r="1"/><circle cx="14" cy="14" r="1"/><circle cx="17" cy="15" r="1"/><circle cx="20" cy="15" r="1"/><circle cx="16" cy="18" r="1"/><circle cx="19" cy="18" r="1"/></svg></span><span class="use-area__name">SHOWER</span></li>
      <li class="use-area"><span class="use-area__tile"><svg viewBox="0 0 24 24" fill="#2f7f2f"><rect x="14" y="3" width="6" height="9" rx="1"/><path d="M3 11h17c0 4-3 6-6 6l1 4H8l1-4c-3-1-6-3-6-6z"/></svg></span><span class="use-area__name">TOILET</span></li>
      <li class="use-area"><span class="use-area__tile"><svg viewBox="0 0 24 24" fill="#2f7f2f"><rect x="2" y="3" width="5" height="4"/><rect x="8" y="3" width="4" height="4"/><path d="M15 7l3-4 3 4z"/><rect x="2" y="10" width="9" height="4"/><rect x="2" y="16" width="9" height="5"/><rect x="13" y="10" width="9" height="11" fill="none" stroke="#2f7f2f" stroke-width="1.5"/><rect x="15" y="14" width="5" height="4"/></svg></span><span class="use-area__name">KITCHEN</span></li>
    </ul>
    <p class="volume">1 Litre (34 Oz.)</p>
  </section>

</main>
</body>
</html>
```